BrimTaps.com

Hey guys!

We are looking for an innovative 1 page web design for our PPC network website - http://quillpeekshot.example/4k82vmtq7r
We are a PPC social media start up, which works with many social media publishers worldwide.
The design must be clean, flat, trendy, we would like to keep our 1 page design structure, but add your own personal touch-up.

We would like you to make it look like a Million $ company.

Good luck!

Target Market(s)

Big Internet Advertising Companies

Number of Pages Required

1 page

```html
<!DOCTYPE html>
<html lang="en">
<head>
<meta charset="utf-8">
<title>BrimTaps.com – Advertise</title>
<link rel="stylesheet" href="https://fonts.googleapis.com/css2?family=Open+Sans:wght@300;400;600;700&display=swap">
<style>
:root{
  --ink:#333333;
  --text:#777777;
  --accent:#4bb8e2;
  --accent-fill:#5bc4ee;
  --button:#2aa7cf;
  --band:#f2f2f2;
  --line:#d6d6d6;
  --white:#ffffff;
  --device:#2b2b2b;
  --desk:#e9e9e9;
}
*{box-sizing:border-box;margin:0;padding:0}
html,body{width:1200px;height:2223px;overflow:hidden;background:var(--white)}
body{font-family:"Open Sans",Arial,sans-serif;color:var(--text);position:relative}
.abs{position:absolute}
.icon{position:absolute;fill:none;stroke:var(--accent);stroke-width:1.6;stroke-linecap:round;stroke-linejoin:round}

/* Advertise section */
.advertise{position:absolute;left:0;top:0;width:1200px;height:584px;background:var(--white)}
.advertise h1{position:absolute;top:72px;width:100%;text-align:center;font-weight:300;font-size:33px;color:var(--ink)}
.advertise .lead{position:absolute;top:124px;width:100%;text-align:center;font-size:19px;color:#555}
.feature h3{font-size:18px;font-weight:600;color:var(--ink);margin-bottom:10px}
.feature p{font-size:14.5px;line-height:22.5px;width:410px}
.feature strong{color:#555;font-weight:600}

/* How it works */
.how{position:absolute;left:0;top:584px;width:1200px;height:638px;background:var(--band)}
.how h2{position:absolute;left:45px;top:170px;font-size:51px;font-weight:300;color:var(--ink);line-height:60px}
.how .sub{position:absolute;left:45px;top:245px;font-size:32px;font-weight:300;color:#444;line-height:45px;width:330px}
.join{position:absolute;left:45px;top:400px;width:175px;height:47px;border:2px solid var(--button);border-radius:24px;color:var(--button);font-size:11px;font-weight:700;letter-spacing:.5px;display:flex;align-items:center;justify-content:center}
.steps{position:absolute;left:426px;top:76px;width:350px;height:476px;background:var(--white);border:2px solid var(--line);border-radius:18px;overflow:hidden}
.step{height:72px;display:flex;align-items:center;padding-left:22px;font-size:15px;font-weight:600;color:var(--ink);border-bottom:1px solid var(--line)}
.step.active{background:var(--accent-fill);color:var(--white);border-bottom:none}
.step-body{padding:24px 22px 0;height:262px;border-bottom:1px solid var(--line);font-size:14px;line-height:22.5px;color:var(--text)}
.step-body p{margin-bottom:12px}
.step.last{border-bottom:none}
.faq h3{font-size:18px;font-weight:600;color:var(--ink);margin-bottom:12px}
.faq p{font-size:14px;line-height:22.5px;width:350px}

/* Tools */
.device{position:absolute;left:198px;top:1280px;width:777px;height:216px;border-radius:10px 10px 0 0;background:linear-gradient(180deg,#2b2b2b 0,#2b2b2b 70%,#dcdcdc 70%,#e6e6e6 100%)}
.tools h2{position:absolute;top:1528px;width:100%;text-align:center;font-size:31px;font-weight:300;color:var(--ink)}
.tools .intro{position:absolute;left:225px;top:1614px;width:750px;text-align:center;font-size:21px;line-height:28.5px;color:#555}
.tool{position:absolute;top:1790px;width:260px}
.tool h3{font-size:18.5px;font-weight:600;color:var(--ink);margin-bottom:10px}
.tool p{font-size:14.5px;line-height:23px}
.desk{position:absolute;left:0;top:1988px;width:1200px;height:235px;background:linear-gradient(180deg,#ffffff 0,var(--desk) 100%)}
</style>
</head>
<body>

<section class="advertise">
  <h1>Advertise On BrimTaps</h1>
  <p class="lead">The regular search engine PPC advertising is NOT working anymore. Find out why you should work with us:</p>

  <svg class="icon" style="left:80px;top:208px" width="64" height="48" viewBox="0 0 64 48">
    <circle cx="24" cy="24" r="21"/><circle cx="24" cy="24" r="15"/><circle cx="24" cy="24" r="9"/><circle cx="24" cy="24" r="3"/>
    <path d="M24 24H62M56 19l6 5-6 5"/>
  </svg>
  <div class="feature abs" style="left:180px;top:208px">
    <h3>Professional Ads Optimization</h3>
    <p>Our social media experts take care of your ads 24/7, optimizing every single aspect to perfectly suit your social media campaign needs.</p>
  </div>

  <svg class="icon" style="left:655px;top:208px" width="52" height="52" viewBox="0 0 52 52">
    <rect x="3" y="4" width="46" height="32"/><path d="M10 28l10-9 8 6 14-14M36 11h6v6M26 36v12M18 48h16"/>
  </svg>
  <div class="feature abs" style="left:750px;top:208px">
    <h3>State Of The Art Performance Analyzing</h3>
    <p>Gain advantage of BrimTaps extraordinary reports analyzing platform. Track and monitor every single visitor, analyze your campaigns engagement across the worldwide Social Media followers. <strong>Campaign insights at its best.</strong></p>
  </div>

  <svg class="icon" style="left:80px;top:376px" width="64" height="52" viewBox="0 0 64 52">
    <circle cx="6" cy="46" r="4"/><circle cx="24" cy="24" r="4"/><circle cx="38" cy="32" r="4"/><circle cx="58" cy="6" r="4"/>
    <path d="M8.5 43l13-16M27.5 26l7 4M40.5 29l15-20"/>
  </svg>
  <div class="feature abs" style="left:180px;top:376px">
    <h3>Increase Your ROI</h3>
    <p>You can expect better performance for your advertising campaign - Lower CPC budget (instead of wasting tons of money on the conventional PPC campaign), more targeted traffic reach, which maximizes your ROI.</p>
  </div>

  <svg class="icon" style="left:657px;top:376px" width="48" height="48" viewBox="0 0 48 48">
    <circle cx="24" cy="24" r="21"/><circle cx="24" cy="24" r="16"/><path d="M24 24l6-10M24 11v3M13 24h3M32 24h3"/><rect x="19" y="31" width="10" height="5" rx="1"/>
  </svg>
  <div class="feature abs" style="left:750px;top:376px">
    <h3>Drive Traffic Within Minutes</h3>
    <p>Our active, motivated and reputed publishers are waiting to spread your content online with their millions of followers. All you need is to sit down and watch the traffic flow to your desired website.</p>
  </div>
</section>

<section class="how">
  <svg class="icon" style="left:45px;top:126px" width="38" height="44" viewBox="0 0 38 44">
    <circle cx="19" cy="7" r="4"/><path d="M19 3V0M16.5 10L5 40M21.5 10L33 40M8 30c7 5 15 5 22 0"/>
  </svg>
  <svg class="icon" style="left:120px;top:126px" width="34" height="44" viewBox="0 0 34 44">
    <path d="M11 32c0-6-8-9-8-18a14 14 0 0 1 28 0c0 9-8 12-8 18zM12 36h10M13 40h8"/>
  </svg>
  <svg class="icon" style="left:200px;top:126px" width="56" height="44" viewBox="0 0 56 44">
    <path d="M2 14l16-6 20 6 16-6v32l-16 6-20-6-16 6z M18 8v32M38 14v32"/><circle cx="28" cy="14" r="6"/><path d="M28 20v8"/>
  </svg>
  <h2>How It Works?</h2>
  <p class="sub">Follow How BrimTaps Unique Program Operates</p>
  <div class="join">JOIN OUR TEAM!</div>

  <div class="steps">
    <div class="step">Signing Up</div>
    <div class="step active">Choose Relevant Content</div>
    <div class="step-body">
      <p>After you've created your account with BrimTaps, you'll be able to log in to your publisher account area. At your publisher panel, choose the content that is relevant to your audience from our wide variety article archive.</p>
      <p>Share the content on your social networks, blogs and websites, spread it online with your followers and get paid for it!</p>
    </div>
    <div class="step last">Get Paid</div>
  </div>

  <svg class="icon" style="left:806px;top:76px" width="44" height="46" viewBox="0 0 44 46">
    <path d="M12 2v44M2 6h28l6 5-6 5H2zM22 20H8l-5 5 5 5h14z"/>
  </svg>
  <div class="faq abs" style="left:806px;top:140px">
    <h3>So How Am I Making Money?</h3>
    <p>Good question! Our advanced tracking system monitors each individual click your unique link has generated. For each click, you get paid!</p>
  </div>
  <svg class="icon" style="left:806px;top:286px" width="54" height="46" viewBox="0 0 54 46">
    <path d="M4 10h44v32H4zM4 10l32-8 4 8M36 22h14v10H36z"/><circle cx="41" cy="27" r="1.5"/>
  </svg>
  <div class="faq abs" style="left:806px;top:348px">
    <h3>Cool, but how much?</h3>
    <p>It depends on a few factors - Where your clicks came from (Countries), the amounts of clicks and the price per click for each individual. More advanced aspects are responsible for calculation of each single campaign click.</p>
  </div>
</section>

<section class="tools">
  <div class="device" role="img" aria-label="Desktop monitor showing the BrimTaps publisher dashboard"></div>
  <h2>Let BrimTaps Works For You</h2>
  <p class="intro">Once you become a part of BrimTaps family, we have a mutual goal - To maximize both sides revenue. Therefore, we have to provide you with the best monetization and management tools available in the entire industry. As a result, our team have developed a unique Chatterly Application to cover all your needs.</p>

  <div class="tool" style="left:30px">
    <h3>Auto-Post Links</h3>
    <p>Control multiple pages with a click of a button. You get the power to schedule &amp; reschedule links days ahead. Stop wasting time with "old fashion" style.</p>
  </div>
  <div class="tool" style="left:315px">
    <h3>Increase Links Reach</h3>
    <p>ou know what works best for your pages and audience. Choose between the regular Link Share and Image post attached with your campaign URL.</p>
  </div>
  <div class="tool" style="left:600px">
    <h3>Easy Page Management</h3>
    <p>No matter how many pages you have, BrimTaps gives you the best management tools available - Monitor and control your page posts from one screen only.</p>
  </div>
  <div class="tool" style="left:885px">
    <h3>Personal Assistant</h3>
    <p>BrimTaps provides you with your own real personal assistant who keeps you updated about the latest news and trends.</p>
  </div>

  <div class="desk" role="img" aria-label="Flat desk scene with notebook, sunglasses, sticky note, marker, keyboard, mouse, scissors and tape"></div>
</section>

</body>
</html>
```